Quillmarsh Property Solutions need a business card design

Hello guys. We would need a business card design asap please.
We are a start up property investment business based in London UK specialised in buying, selling, managing and letting properties and helping distressed property owners.
The name of our Business is Quillmarsh, the logo symbolises the four fundamental elements of the world (earth, air, fire and water) and so it stands for strength, stability, longevity.
We would like the business card to communicate professionalism and reliability. Many many thanks indeed for your work.

Details:

1.) Rosalind Updike
Property Investor
Mobile: +44(0)7700123456
Email: rosalind.quillmarsh@mailbox-example.com

2.) Dominic Updike
Property Investor
Mobile: +44(0)7700987654
Email: dominic.quillmarsh@mailbox-example.com

```html
<!DOCTYPE html>
<html lang="en">
<head>
<meta charset="utf-8">
<title>Quillmarsh Property Solutions — Business Card</title>
<link rel="stylesheet" href="https://fonts.googleapis.com/css2?family=Jost:wght@500;700&family=PT+Sans:wght@400;700&display=swap">
<style>
  :root {
    --backdrop: #e4e4ea;
    --card: #ffffff;
    --ink: #111111;
    --brand-red: #c0283a;
    --brand-blue: #2f5fb0;
    --brand-green: #1f6b36;
    --text-grey: #5a5a5a;
    --divider: #c9c9c9;
  }
  * { box-sizing: border-box; margin: 0; padding: 0; }
  html, body {
    width: 1200px; height: 987px; overflow: hidden;
    background: var(--backdrop);
  }
  .canvas {
    position: relative; width: 1200px; height: 987px;
  }
  .card {
    position: absolute; left: 250px; width: 700px; height: 400px;
    background: var(--card); border-radius: 28px; overflow: hidden;
    box-shadow: 0 6px 18px rgba(0,0,0,0.12);
  }
  .card--front { top: 50px; }
  .card--back { top: 537px; }

  /* front */
  .front__band {
    position: absolute; left: 0; right: 0; bottom: 0; height: 72px;
    background: var(--brand-red);
  }
  .front__rule {
    position: absolute; left: 0; right: 0; bottom: 78px; height: 3px;
    background: var(--brand-green);
  }
  .brand {
    position: absolute; left: 48px; top: 120px; width: 260px;
  }
  .brand__row { display: flex; align-items: center; gap: 10px; }
  .brand__mark {
    width: 16px; height: 16px; background: var(--brand-red);
  }
  .brand__name {
    font-family: "Jost", sans-serif; font-weight: 700; font-size: 34px;
    letter-spacing: 1px; color: var(--ink); line-height: 1;
  }
  .brand__tagline {
    margin-top: 8px; margin-left: 26px;
    font-family: "Jost", sans-serif; font-weight: 500; font-size: 13px;
    letter-spacing: 1.5px; color: var(--ink);
  }
  .front__divider {
    position: absolute; left: 322px; top: 60px; width: 2px; height: 210px;
    background: linear-gradient(to bottom, rgba(201,201,201,0), var(--divider) 40%, var(--divider) 60%, rgba(201,201,201,0));
  }
  .contact {
    position: absolute; left: 348px; top: 96px; right: 20px;
    font-family: "PT Sans", sans-serif;
  }
  .contact__name {
    font-weight: 700; font-size: 30px; color: var(--brand-red); line-height: 1.1;
  }
  .contact__role {
    font-size: 21px; color: var(--brand-blue); margin-bottom: 22px;
  }
  .contact__line {
    display: flex; align-items: center; gap: 10px;
    color: var(--text-grey); margin-top: 10px;
  }
  .contact__line--phone { font-size: 22px; }
  .contact__line--email { font-size: 17px; }
  .contact__icon { width: 20px; height: 20px; flex: none; }

  /* back */
  .back__content {
    position: absolute; inset: 0;
    display: flex; flex-direction: column; justify-content: center; align-items: center;
  }
  .back__name {
    font-family: "Jost", sans-serif; font-weight: 700; font-size: 76px;
    letter-spacing: 4px; color: var(--ink); line-height: 1;
  }
  .back__tagline {
    margin-top: 14px;
    font-family: "Jost", sans-serif; font-weight: 500; font-size: 30px;
    letter-spacing: 3px; color: var(--ink);
  }
</style>
</head>
<body>
<main class="canvas">

  <section class="card card--front" aria-label="Business card front">
    <div class="brand">
      <div class="brand__row">
        <span class="brand__mark"></span>
        <span class="brand__name">QUILLMARSH</span>
      </div>
      <div class="brand__tagline">PROPERTY SOLUTIONS</div>
    </div>

    <div class="front__divider"></div>

    <div class="contact">
      <div class="contact__name">Dominic Updike</div>
      <div class="contact__role">Property Investor</div>
      <div class="contact__line contact__line--phone">
        <svg class="contact__icon" viewBox="0 0 20 20" aria-hidden="true">
          <rect x="5" y="1" width="10" height="18" rx="2" fill="var(--brand-blue)"/>
          <rect x="7" y="4" width="6" height="6" fill="#fff"/>
          <circle cx="10" cy="15" r="1.5" fill="#fff"/>
        </svg>
        <span>+44(0)7700987654</span>
      </div>
      <div class="contact__line contact__line--email">
        <svg class="contact__icon" viewBox="0 0 20 20" aria-hidden="true">
          <rect x="1" y="4" width="18" height="12" rx="2" fill="var(--brand-blue)"/>
          <path d="M2 5 L10 11 L18 5" stroke="#fff" stroke-width="1.6" fill="none"/>
        </svg>
        <span>dominic.quillmarsh@mailbox-example.com</span>
      </div>
    </div>

    <div class="front__rule"></div>
    <div class="front__band"></div>
  </section>

  <section class="card card--back" aria-label="Business card back">
    <div class="back__content">
      <div class="back__name">QUILLMARSH</div>
      <div class="back__tagline">PROPERTY SOLUTIONS</div>
    </div>
  </section>

</main>
</body>
</html>
```